Design NEW business card

We would like a business card using the colour deep red wine or dark navy blue textured background (patterned or not, open to suggestions) with a high gloss debossed rose gold/copper RM Roland Mercer Jewellery business name (Provided). I have included images for your review we would like to keep our currently logo and business name on the front but you can change the layout and positioning. For the back of the card we are open to all suggestions/variations.
Business
Use our current RM Roland Mercer Jewellery logo (Provided image)

```html
<!DOCTYPE html>
<html lang="en">
<head>
<meta charset="utf-8">
<title>Roland Mercer Jewellery – Business Card</title>
<link rel="stylesheet" href="https://fonts.googleapis.com/css2?family=Roboto:wght@300;400;500&display=swap">
<style>
  :root {
    --backdrop: #e4e4e4;
    --card-white: #f7f7f6;
    --wine: #5b2329;
    --copper: #b07a58;
    --copper-soft: #c4906d;
    --ink: #3f3f3f;
    --muted: #a9a9a9;
    --rule: #c9c9c9;
  }
  * { box-sizing: border-box; margin: 0; padding: 0; }
  html, body { width: 1200px; height: 960px; overflow: hidden; }
  body {
    background: var(--backdrop);
    font-family: "Roboto", Arial, sans-serif;
    position: relative;
  }
  .card {
    position: absolute;
    width: 600px;
    height: 343px;
    box-shadow: 0 2px 4px rgba(0,0,0,0.35);
  }
  .card--front { left: 314px; top: 113px; background: var(--card-white); }
  .card--back  { left: 311px; top: 472px; background: var(--wine); }

  /* Brand lockup: plain circle + name, filling the mark's area */
  .brand {
    position: absolute;
    display: flex;
    align-items: center;
    justify-content: center;
  }
  .brand__dot {
    flex: none;
    border-radius: 50%;
    border: 1.5px solid var(--copper);
  }
  .brand__name {
    font-family: "Roboto", Arial, sans-serif;
    font-weight: 300;
    color: var(--copper);
    text-transform: uppercase;
    text-align: center;
    white-space: nowrap;
  }
  .brand__name span { display: block; }
  .brand__line--sub { letter-spacing: 0.9em; margin-right: -0.9em; }

  .card--front .brand {
    left: 40px; top: 100px; width: 270px; height: 150px;
  }
  .card--front .brand__dot { width: 52px; height: 52px; margin-right: 16px; }
  .card--front .brand__name { font-size: 17px; letter-spacing: 3px; line-height: 1.7; }
  .card--front .brand__line--sub { font-size: 10px; }

  .card--back .brand {
    left: 100px; top: 70px; width: 400px; height: 200px;
  }
  .card--back .brand__dot {
    width: 80px; height: 80px; margin-right: 24px;
    border-color: var(--copper-soft);
  }
  .card--back .brand__name { font-size: 23px; letter-spacing: 4px; line-height: 1.7; color: var(--copper-soft); }
  .card--back .brand__line--sub { font-size: 12px; }

  .divider {
    position: absolute;
    left: 327px; top: 72px;
    width: 1px; height: 200px;
    background: var(--rule);
  }
  .contact {
    position: absolute;
    left: 357px; top: 72px;
  }
  .contact__name {
    font-size: 20px; font-weight: 500;
    color: var(--copper); letter-spacing: 0.2px;
    line-height: 24px;
  }
  .contact__role {
    font-size: 14px; color: var(--muted);
    line-height: 20px;
  }
  .contact__address {
    margin-top: 9px;
    font-size: 14.5px; color: var(--ink);
    line-height: 19px;
  }
  .contact__list {
    list-style: none;
    margin-top: 12px;
  }
  .contact__list li {
    display: flex; align-items: center;
    font-size: 14.5px; color: var(--ink);
    line-height: 19px; height: 19px;
  }
  .contact__list svg {
    width: 13px; height: 13px;
    margin-right: 10px;
    fill: var(--copper);
    flex: none;
  }
</style>
</head>
<body>

<section class="card card--front" aria-label="Card front">
  <div class="brand">
    <span class="brand__dot" aria-hidden="true"></span>
    <p class="brand__name">
      <span class="brand__line">Roland Mercer</span>
      <span class="brand__line brand__line--sub">Jewellery</span>
    </p>
  </div>

  <div class="divider"></div>

  <div class="contact">
    <p class="contact__name">DANIEL HART</p>
    <p class="contact__role">CEO/FOUNDER</p>
    <p class="contact__address">1243 Willowbend Road<br>Fairbanks, Alaska 99712</p>
    <ul class="contact__list">
      <li>
        <svg viewBox="0 0 16 16" aria-hidden="true"><path d="M3.2 1.2l2.4 2.6-1.2 2.1c.9 1.9 2.3 3.4 4.2 4.4l2.1-1.2 2.6 2.4-1.3 2.5C6.6 13.8 2 9.2 1 3.4z"/></svg>
        555 210 4871
      </li>
      <li>
        <svg viewBox="0 0 16 16" aria-hidden="true"><path d="M4.5 0.5h7a1 1 0 0 1 1 1v13a1 1 0 0 1-1 1h-7a1 1 0 0 1-1-1v-13a1 1 0 0 1 1-1zm.8 2v9.5h5.4V2.5zM8 13a.8.8 0 1 0 0 1.6A.8.8 0 0 0 8 13z"/></svg>
        555 382 6190
      </li>
      <li>
        <svg viewBox="0 0 16 16" aria-hidden="true"><path d="M4 1h8v4H4zM1.5 6h13a1 1 0 0 1 1 1v5h-2v3h-11v-3h-2V7a1 1 0 0 1 1-1zm3.5 5v2.5h6V11z"/></svg>
        555 734 2058
      </li>
      <li>
        <svg viewBox="0 0 16 16" aria-hidden="true"><path d="M1 3h14v1.2L8 8.6 1 4.2zm0 2.6l7 4.4 7-4.4V13H1z"/></svg>
        hello@rolandmercer.com
      </li>
      <li>
        <svg viewBox="0 0 16 16" aria-hidden="true"><path d="M8 1a7 7 0 1 0 0 14A7 7 0 0 0 8 1zm-1 2.3c-.6.9-1.6 1.4-1.7 2.6.9.3 1.8.9 1.8 2-.1 1-1.2 1.3-1.1 2.4l.5 2.2A5.6 5.6 0 0 1 2.5 8 5.5 5.5 0 0 1 7 3.3zm3 .5a5.6 5.6 0 0 1 2.9 6.6c-.7-.6-1.3-1.5-2.3-1.4-.9.1-1.4-1.2-.9-2 .5-.8 0-1.9.3-3.2z"/></svg>
        www.rolandmercer.com
      </li>
    </ul>
  </div>
</section>

<section class="card card--back" aria-label="Card back">
  <div class="brand">
    <span class="brand__dot" aria-hidden="true"></span>
    <p class="brand__name">
      <span class="brand__line">Roland Mercer</span>
      <span class="brand__line brand__line--sub">Jewellery</span>
    </p>
  </div>
</section>

</body>
</html>
```